Need A Modern Website Design For ADSL2+ Provider

AIM: To sell affordable combined ADSL2+ Unlimited & phone line rentals to residential customers.

TYPE: This project is for DESIGN only (no code)

Source Files: I need all source files, fonts, images to be provided in ZIP format.

Logo: Existing (attached)

-Corporate Colours-
Black & Red (Same as Logo)
Others colours are fine as long as it looks corporate and modern.

-Pages-
Need another page to display our pricing plan

(1)Homepage Design
(2)Page to display our plans (needs to be in tables)
Example: http://lnkrip.example/QwTr8k

-Pricing Plan-
(1) $59.95 / Month (Metro / City Areas)
(2) $79.95 / Month (Outside City Areas / Rural Areas)
Detailed Pricing plans is in PDF attached
Updates

Just letting everyone know we have picked a designer, thank you for all you submissions.

Target Market(s)

Both male & female, Young & Old

Industry/Entity Type

Residential

Requirements
Must have
• + Graphic banner on the home page that shows our ADSL2+ combo plan for ADSL2+ Unlimited & Phone Line Rental for only $59.95

+ A box to allow customers to login to their account (username & password + login button)

+ Clearly display contact number
+ Button to sign up
+ Button to check service availability something like https://checkline.vobbern.example/wizard/

+ Button for Live Chat
+ Navigation menu
+ Social media icons Pagebook, Zentra +, Chirpel
+ Minimal text on homepage
+ Corporate & Friendly
Nice to have
• + Effective use of icons with corporate colours
+ Effective use of stockphotos
(use of people in photos would be nice)

+ Effective use of graphics to navigate people through the site and inform customers of specials,etc.
Should not have
• + Cluttered
+ Don’t want long scrolling homepage
+ Don’t want too much text on homepage 500 words is the estimate max.

```html
<!DOCTYPE html>
<html lang="en">
<head>
<meta charset="utf-8">
<title>Vantrel – Home</title>
<link rel="stylesheet" href="https://fonts.googleapis.com/css2?family=Jost:ital,wght@0,400;0,500;1,700;1,800&family=Francois+One&family=Cinzel:wght@500&display=swap">
<style>
  :root {
    --ink: #231f20;
    --red: #ee3a3a;
    --sky: #3fbfe0;
    --white: #ffffff;
    --grey-text: #8c8c8c;
    --dark-band: #2b2b2b;
    --dark-band-2: #4a4a4a;
    --field-border: #9a9a9a;
  }
  * { box-sizing: border-box; margin: 0; padding: 0; }
  html, body { width: 1200px; height: 909px; overflow: hidden; background: var(--white); }
  body { position: relative; font-family: "Jost", sans-serif; color: var(--ink); }
  .abs { position: absolute; }

  /* Header */
  .brand { left: 10px; top: 28px; display: flex; align-items: center; gap: 16px; }
  .brand-dot { width: 97px; height: 97px; border-radius: 50%; background: var(--ink); }
  .brand-name { font-family: "Cinzel", serif; font-weight: 500; font-size: 74px; color: var(--ink); letter-spacing: 2px; line-height: 1; }
  .main-nav a { position: absolute; top: 66px; font-size: 21px; color: var(--ink); text-decoration: none; transform: translateX(-50%); }
  .nav-active::after { content: ""; position: absolute; left: -12px; right: -12px; top: 35px; height: 4px; background: var(--red); }
  .search { border: 2px solid var(--field-border); border-radius: 12px; font-size: 15px; color: var(--grey-text); padding: 0 14px; line-height: 18px; }
  .header-search { left: 976px; top: 71px; width: 169px; height: 23px; }

  /* Login band */
  .band { background: linear-gradient(100deg, var(--dark-band) 0%, var(--dark-band-2) 50%, var(--dark-band) 100%); }
  .login-band { left: 10px; top: 141px; width: 1180px; height: 84px; }
  .login-label { left: 40px; top: 170px; color: var(--white); font-size: 19px; }
  .field { left: 99px; width: 169px; height: 22px; background: var(--white); border-radius: 11px; color: var(--red); font-size: 15px; text-align: center; line-height: 22px; }
  .go { left: 278px; top: 167px; width: 38px; height: 34px; background: var(--sky); color: var(--white); font-family: "Francois One", sans-serif; font-size: 20px; text-align: center; line-height: 34px; }
  .contact { left: 855px; top: 170px; color: var(--white); font-size: 20px; }

  /* Banner */
  .banner { left: 10px; top: 238px; width: 1180px; height: 324px; background: linear-gradient(180deg, #2a2a2a 0%, #9a9a9a 38%, #f2f2f2 72%, #ffffff 100%); }
  .display { font-family: "Francois One", sans-serif; }
  .plan-card { top: 299px; width: 242px; height: 220px; background: var(--sky); border-radius: 14px; text-align: center; }
  .plan-title { font-size: 54px; color: var(--white); line-height: 1; margin-top: 14px; }
  .plan-from { font-size: 24px; margin-top: 12px; line-height: 1; }
  .plan-price { font-size: 66px; color: var(--red); line-height: 1; margin-top: 6px; }
  .plan-price sup { font-size: 28px; color: var(--ink); vertical-align: 28px; margin-right: 2px; }
  .plan-net { font-size: 24px; line-height: 1; margin-top: 4px; }
  .combo { left: 395px; top: 306px; width: 380px; text-align: center; }
  .combo-title { font-size: 56px; color: var(--red); line-height: 1; }
  .combo-text { font-size: 26px; line-height: 30px; margin-top: 18px; color: #333; letter-spacing: 0.6px; }
  .btn { background: var(--sky); color: var(--white); border-radius: 4px; text-align: center; font-family: "Francois One", sans-serif; }
  .learn-more { left: 497px; top: 457px; width: 180px; height: 48px; font-size: 26px; line-height: 48px; }
  .pager { left: 19px; top: 531px; display: flex; align-items: center; gap: 8px; font-weight: 500; font-size: 15px; }

  .rule { left: 10px; top: 562px; width: 1180px; height: 9px; background: var(--sky); }

  /* Advantage */
  .adv-title { left: 40px; top: 580px; font-size: 26px; color: #333; font-weight: 400; }
  .adv-list { left: 63px; top: 616px; list-style: none; font-style: italic; font-weight: 800; font-size: 17px; line-height: 21px; color: #333; }
  .adv-list li::before { content: "• "; }
  .router-signal { left: 500px; top: 582px; width: 92px; height: 118px; border-radius: 10px; background: radial-gradient(circle at 50% 30%, #dff3fa 0%, #f1f1f1 75%); }
  .router-body { left: 520px; top: 704px; width: 162px; height: 48px; border-radius: 12px; background: linear-gradient(180deg, #f3f3f3 0%, #e2e2e2 100%); }
  .easy { left: 572px; top: 648px; font-size: 27px; color: #b5b5b5; }
  .signup { left: 849px; top: 596px; font-size: 58px; color: #8a8a8a; }
  .click-here { left: 903px; top: 678px; width: 180px; height: 48px; font-size: 32px; line-height: 48px; }

  /* Footer */
  .site-footer { left: 10px; top: 778px; width: 1180px; height: 131px; }
  .footer-search { left: 91px; top: 810px; width: 169px; height: 23px; border-color: #bbb; color: #aaa; }
  .footer-nav a { position: absolute; top: 808px; font-size: 21px; color: var(--white); text-decoration: none; transform: translateX(-50%); white-space: nowrap; }
  .legal { left: 342px; top: 855px; width: 600px; text-align: center; color: var(--white); font-size: 14px; line-height: 17px; }
  .follow { left: 1040px; top: 806px; width: 141px; height: 89px; background: var(--white); border-radius: 6px; text-align: center; }
  .follow-title { color: var(--sky); font-size: 16px; margin-top: 4px; }
  .social { display: flex; justify-content: center; gap: 6px; margin-top: 8px; }
  .social span { display: flex; align-items: center; gap: 3px; font-size: 12px; color: var(--ink); }
  .social i { width: 14px; height: 14px; background: var(--sky); display: inline-block; }
</style>
</head>
<body>
  <header>
    <div class="abs brand"><span class="brand-dot"></span><span class="brand-name">VANTREL</span></div>
    <nav class="main-nav">
      <a href="#" class="nav-active" style="left:577px">Home</a>
      <a href="#" style="left:688px">About</a>
      <a href="#" style="left:786px">Plans</a>
      <a href="#" style="left:897px">Support</a>
    </nav>
    <div class="abs search header-search">Search for....</div>
  </header>

  <section>
    <div class="abs band login-band"></div>
    <div class="abs login-label">Login</div>
    <div class="abs field" style="top:157px">User Name</div>
    <div class="abs field" style="top:190px">Password</div>
    <div class="abs go">Go</div>
    <div class="abs contact">Contact us 1300 55-18-90</div>
  </section>

  <section class="display">
    <div class="abs banner"></div>
    <div class="abs plan-card" style="left:99px">
      <div class="plan-title">Metro</div>
      <div class="plan-from">Starting at.</div>
      <div class="plan-price"><sup>$</sup>59.95</div>
      <div class="plan-net">On Net.</div>
    </div>
    <div class="abs combo">
      <div class="combo-title">Pairo2+</div>
      <div class="combo-text">Pairo2+ offers line rental with Unlimited ADSL2+ Broadband.</div>
    </div>
    <div class="abs btn learn-more">Learn More</div>
    <div class="abs plan-card" style="left:852px">
      <div class="plan-title">Regional</div>
      <div class="plan-from">Starting at.</div>
      <div class="plan-price"><sup>$</sup>79.95</div>
      <div class="plan-net">Off Net.</div>
    </div>
    <div class="abs pager">
      <span>Back</span>
      <svg width="42" height="20" viewBox="0 0 42 20"><polygon points="18,0 18,20 0,10" fill="#999"/><polygon points="24,0 24,20 42,10" fill="#999"/></svg>
      <span>Next</span>
    </div>
  </section>

  <div class="abs rule"></div>

  <section>
    <h2 class="abs display adv-title">The Vantrel Advantage</h2>
    <ul class="abs adv-list">
      <li>Free installation</li>
      <li>Unlimited ADSL2+</li>
      <li>line rental included</li>
      <li>WIFI Modem included</li>
      <li>Minimum Monthly Charge</li>
      <li>Low monthly administartion fee</li>
      <li>Local, long distance, and mobile calling</li>
    </ul>
    <div class="abs router-signal" role="img" aria-label="Illustration of wireless signal waves above a modem antenna"></div>
    <div class="abs router-body" role="img" aria-label="Illustration of a wireless modem with status lights"></div>
    <div class="abs display easy">It's easy as 1,2,3</div>
    <div class="abs display signup">Sign up now</div>
    <div class="abs btn click-here">Click here</div>
  </section>

  <footer>
    <div class="abs band site-footer"></div>
    <div class="abs search footer-search">Search for....</div>
    <nav class="footer-nav">
      <a href="#" class="nav-active" style="left:334px">Home</a>
      <a href="#" style="left:445px">About</a>
      <a href="#" style="left:545px">Plans</a>
      <a href="#" style="left:655px">Support</a>
      <a href="#" style="left:780px">Contact us</a>
      <a href="#" style="left:917px">Mobile Site</a>
    </nav>
    <div class="abs legal">Vantrel Communication and Information Services Pty Limited ABN<br>2013 all rights reserved</div>
    <div class="abs follow">
      <div class="follow-title">Follow us</div>
      <div class="social">
        <span><i></i>Chirpel</span>
        <span><i></i>Pagebook</span>
      </div>
    </div>
  </footer>
</body>
</html>
```